Briloran Clear Springs needs a new business card design (we produce and sell pure bottled water)

We need a clean modern design for our new business cards, We have an existing logo which ultimately cannot be changed, however it could be slighty improved and the colours adjusted. We have this existing logo on all of our bottles, vehicles etc.

Our company slogan is "Pure down to the last drop".
Along with our relevant company information
(Address, phone, website email etc) we will only be using names and not putting position titles for flexibilty.

We are looking for a clean, minimalist modern design.

You can view our website (if need of an update also!) to see our business.

Industry/Entity Type

Business

Contact Information for Business Card

Staff Name : XXXXXX XXXXXX
Address : 9/41 Tavenor St
Halden Rise QLD 4172
Staff Mobile Number : 04XX XXX XXX
Office Phone Number : 07 3918 2457
Staff Email Address : XXXX@brilorancleargo.com.au
Website : www.brilorancleargo.com.au

Font styles to use
Sans Serif

Colors
cee9f5
33a6d7
0492cd
0455a3
3276b5
85abd2
cedeed

Requirements
Must have
• The ability to edit and change the staff members details as we will need to edit for each respective staff member (7 in total)

```html
<!DOCTYPE html>
<html lang="en">
<head>
<meta charset="utf-8">
<title>Briloran Clear Springs – Business Card</title>
<link href="https://fonts.googleapis.com/css2?family=Source+Sans+3:wght@400;600;700&display=swap" rel="stylesheet">
<style>
  :root {
    --backdrop: #e8e8e8;
    --card: #232427;
    --text: #f2f2f2;
    --brand: #0492cd;
    --brand-light: #33a6d7;
    --icon: #3276b5;
    --divider: #3a3b3f;
  }
  * { margin: 0; padding: 0; box-sizing: border-box; }
  html, body { width: 1200px; height: 900px; overflow: hidden; }
  body {
    background: var(--backdrop);
    position: relative;
    font-family: "Source Sans 3", sans-serif;
    color: var(--text);
  }
  .card {
    position: absolute;
    top: 271px;
    width: 457px;
    height: 281px;
    background: var(--card);
    border-radius: 14px;
  }
  .card--front { left: 137px; }
  .card--back { left: 626px; }

  .brand-block {
    position: absolute;
    left: 46px;
    top: 72px;
    width: 148px;
    height: 138px;
    display: flex;
    flex-direction: column;
    align-items: flex-end;
    justify-content: center;
    gap: 8px;
  }
  .brand-dot {
    width: 22px; height: 22px; border-radius: 50%;
    background: var(--brand);
  }
  .brand-name {
    color: var(--brand);
    font-weight: 700;
    font-size: 23px;
    line-height: 1.02;
    text-align: right;
    text-transform: uppercase;
  }
  .divider {
    position: absolute;
    left: 213px; top: 81px;
    width: 1px; height: 130px;
    background: var(--divider);
  }
  .details { position: absolute; left: 236px; top: 67px; }
  .staff-name { font-size: 19px; font-weight: 600; line-height: 24px; margin-bottom: 4px; }
  .address { font-size: 13px; line-height: 17px; margin-bottom: 9px; }
  .contact-list { list-style: none; font-size: 13px; line-height: 17.5px; }
  .contact-list li { display: flex; align-items: center; gap: 7px; }
  .contact-list svg { width: 10px; height: 10px; fill: var(--icon); flex: none; }
  .website { font-size: 13px; margin-top: 8px; margin-left: -2px; }

  .back-mark {
    position: absolute; inset: 0;
    display: flex; align-items: center; justify-content: center; gap: 18px;
  }
  .back-mark .brand-dot { width: 44px; height: 44px; }
  .back-mark .brand-name { font-size: 40px; text-align: left; }
</style>
</head>
<body>
  <section class="card card--front" aria-label="Business card front">
    <div class="brand-block">
      <span class="brand-dot"></span>
      <span class="brand-name">Briloran<br>Clear<br>Springs</span>
    </div>
    <div class="divider"></div>
    <div class="details">
      <p class="staff-name">Maren Talbott</p>
      <p class="address">9/41 Tavenor St<br>Halden Rise QLD 4172</p>
      <ul class="contact-list">
        <li><svg viewBox="0 0 10 10" aria-hidden="true"><path d="M3 0h4a1 1 0 0 1 1 1v8a1 1 0 0 1-1 1H3a1 1 0 0 1-1-1V1a1 1 0 0 1 1-1zm0 1.5v6h4v-6z"/></svg>0400 618 273</li>
        <li><svg viewBox="0 0 10 10" aria-hidden="true"><path d="M2 0.5l2 2.2-1 1.2c.6 1.3 1.6 2.3 2.9 2.9l1.2-1 2.2 2-1.2 1.7C4.6 9.3.7 5.4.3 1.7z"/></svg>07 3918 2457</li>
        <li><svg viewBox="0 0 10 10" aria-hidden="true"><path d="M0 2h10v.8L5 5.6 0 2.8zm0 1.9l5 2.8 5-2.8V8.5H0z"/></svg>info@brilorancleargo.com.au</li>
      </ul>
      <p class="website">www.brilorancleargo.com.au</p>
    </div>
  </section>

  <section class="card card--back" aria-label="Business card back">
    <div class="back-mark">
      <span class="brand-dot"></span>
      <span class="brand-name">Briloran<br>Clear Springs</span>
    </div>
  </section>
</body>
</html>
```